Cannabis Media Network Advertising Kit

Polar Orbit Media is a digital media news network focused on the startups, entrepreneurs and innovative companies in the cannabis industry. We are ready to release our new services for 2017.

We are looking for a modern looking advertising kit created that we would send to our potential clients.

We want it to look similar to our branding. Our website is www.polarorbitmedia.example.

Target Market(s)

Page 3: Audience:
Entrepreneurs, professionals, execs, VC’s, and Investors
Include stats: 34% Female/ 66% Male, 34% 25-34 Years Old $24% 35-44 Years Old

Industry/Entity Type

Media

Font styles to use
Sans Serif

Colors
0555a3
0492cd
ffffff
edf1f7

Requirements
Must have
• Outline Idea is below. Images can be provided.
• Page 1: Header Page (POM logo)
• Leading digital media news network covering the latest tech, startups, and innovative companies in the cannabis industry.
• Page 2: About Us - Mission and Brand
• Polar Orbit Media is the leading digital media platform that is dedicated to profiling the startups, entrepreneurs and innovative companies in the cannabis industry.
• Over the past few years we have been highlighting the upcoming and established businesses in the industry, developed a platform for leaders to share their knowledge and insight, and created
• a spotlight for the innovative technology.
• But most importantly, we have created a community of entrepreneurs, investors and professionals who have the same mission of growing the b2b industry together.
• POM is more than just a network and brand, we are highlighting history in the making of high quality original content.
• Page 3: Audience:
• Entrepreneurs, professionals, execs, VC’s, and Investors
• Include stats: 34% Female/ 66% Male, 34% 25-34 Years Old $24% 35-44 Years Old
• Page 4: POM Original Web Series
• Pre/Post Commercial Opportunities $5,000
• Tinbell Reviews and POM Talks
• Tinbell Reviews is a un-biased product review segment for the wholesalers, online stores, dispensaries and more.
• POM Talks: One on one interview with the upcoming and leading founders offering advice and insight for fellow entrepreneurs.
• Page 5: POM Original Web Series
• Kettles and Kites is a female founder focused web series, where we highlight the leaders, discuss informative topics and latest products.
• Product placement $2,500
• Page 6: POM Original Web Series
• Upside Ledge gives you a peek into the entrepreneur 2.0 and what it is like running a cannabis business.
• See leadership package
• Page 7: Package 1: Foundation $1,000
• 1. Four full platform ads (via QT, ZR, Plonkit, Fernwork, Braxtile)
• 2. POM Article/Company Spotlight (One Newsletter feature and full POM promotion)
• 3. Newsletter Ad (One run, assets provided by client
• Page 8: Package 2: Traction $5,000
• 1. Six full platform ads (via QT, ZR, Plonkit, Fernwork, Braxtile)
• 4. Business of the Month Badge (POM Homepage)
• 5. Three Verbal Video Advertisements ( Three segments, up to 10 seconds each)
• Page 9: Package 3: Leadership $15,000
• 5. Three Video Advertisements (Three segments, 30 second commercial)
• 7. Upside Ledge Full Segment
• Includes promo and full segment promoted and released via POM.
• Page 10: Events Promotion
• Event Package $1,000
• 1. Four full platform ads (via QT include QT Event on POM Page, ZR, Plonkit, Fernwork, Braxtile)
• A la Carte:
• Add event to POM calendar, basic promotion via social media $250
• POMTV Media Sponsor
• Includes co-branded video production of event, exclusive interview with sponsors, and more
• *Cost: To Be Determined
• Page 11: A La Carte
• 1. Event Addition to Calendar (Basic promotion via social media)
• 2. Six full platform ads (via QT, ZR, Plonkit, Fernwork, Braxtile)
• 3. POM Article/Company Spotlight (One Newsletter feature and full POM promotion)
• 4. Newsletter Ad (One run, assets provided by client
• 5. Business of the Month Badge (POM Homepage)
• 6. Three Verbal Video Advertisements ( Three segments, up to 10 seconds each)
• Page 12: Traction
• Profiled on fernwork, orbel daily, spindara, quillstoa, plonkit, zephrame
• 10k+ organic email list of professionals
• 16k+ page views increasing 25% each month
• 18k+ social media followers
• Viewed in all 50 states and 98 countries
• Page 13: Message from the CEO
• “We at POM understand that our industry is different than any other industry out there, we even look at the entrepreneurs and don’t see them just as an entrepreneur but as an entrepreneur 2.0. Why? Because this is the first time in a long time where we have the opportunity to change how an industry is built from the foundation up and each of these individuals are faced with hurdles and challenges we wouldn’t face in any other industry and yet they are doing what it takes to continue to move forward.”
• Page 14: Contact Us
• POM logo:
• We look forward to growing your brand with the Polar Orbit Media! Contact us today at contact@polarorbitmedia.example
Nice to have
• High Res Images from our content. Which we can provide those images, or you can pull from our site and we can send high res after.
Should not have
• Dark Designed.

```html
<!DOCTYPE html>
<html lang="en">
<head>
<meta charset="utf-8">
<title>POM Original Web Series – Upside Ledge</title>
<link rel="stylesheet" href="https://fonts.googleapis.com/css2?family=Open+Sans:wght@300;400;700&display=swap">
<style>
  :root {
    --brand-deep: #0555a3;
    --brand-bright: #0492cd;
    --white: #ffffff;
    --paper: #edf1f7;
    --ink: #2b2b2b;
    --muted: #444a52;
  }
  html, body {
    margin: 0;
    padding: 0;
    width: 1200px;
    height: 900px;
    overflow: hidden;
    background: var(--paper);
  }
  .page {
    position: relative;
    width: 1200px;
    height: 900px;
    background: var(--paper);
    font-family: "Open Sans", Arial, sans-serif;
    overflow: hidden;
  }
  .page-graphics {
    position: absolute;
    inset: 0;
    width: 1200px;
    height: 900px;
  }
  .section-badge {
    position: absolute;
    left: 49px;
    top: 99px;
    width: 206px;
    height: 206px;
    display: flex;
    align-items: center;
    justify-content: center;
    text-align: center;
    margin: 0;
    color: var(--brand-deep);
    font-weight: 700;
    font-size: 26px;
    line-height: 0.97;
    letter-spacing: -0.2px;
  }
  .content-list {
    position: absolute;
    left: 446px;
    top: 228px;
    width: 560px;
    margin: 0;
    padding: 0;
    list-style: none;
  }
  .content-list li {
    position: relative;
    padding-left: 15px;
    font-size: 19px;
    line-height: 36px;
    font-weight: 400;
    color: var(--muted);
    margin-bottom: 10px;
  }
  .content-list li::before {
    content: "";
    position: absolute;
    left: 0;
    top: 15px;
    width: 7px;
    height: 7px;
    border-radius: 50%;
    background: var(--brand-bright);
  }
  .content-list .package-link {
    color: var(--brand-deep);
  }
  .brand-mark {
    position: absolute;
    left: 1102px;
    top: 806px;
    color: var(--brand-deep);
    font-weight: 700;
    font-size: 22px;
    letter-spacing: 0.5px;
  }
  .page-number {
    position: absolute;
    left: 1148px;
    top: 848px;
    color: var(--ink);
    font-weight: 300;
    font-size: 19px;
  }
</style>
</head>
<body>
<main class="page">
  <svg class="page-graphics" viewBox="0 0 1024 768" xmlns="http://www.w3.org/2000/svg" aria-hidden="true">
    <defs>
      <linearGradient id="facetTone" x1="0" y1="0" x2="1" y2="1">
        <stop offset="0" stop-color="#1f6fc0"/>
        <stop offset="0.5" stop-color="#3d95db"/>
        <stop offset="1" stop-color="#2a7dcc"/>
      </linearGradient>
    </defs>
    <!-- corner header block -->
    <g class="corner-block">
      <circle cx="150" cy="176" r="108" fill="var(--white)"/>
      <polygon points="0,0 222,0 186,48 0,322" fill="url(#facetTone)"/>
      <circle cx="150" cy="176" r="103" fill="url(#facetTone)"/>
      <rect x="0" y="0" width="260" height="310" fill="url(#facetTone)" opacity="0" role="img" aria-label="Faceted blue texture"/>
      <circle cx="130" cy="172" r="88" fill="var(--white)"/>
      <line x1="236" y1="0" x2="184" y2="62" stroke="#0555a3" stroke-width="4"/>
      <line x1="46" y1="268" x2="0" y2="342" stroke="#0492cd" stroke-width="4"/>
    </g>
    <!-- bottom right accents -->
    <g class="corner-accent">
      <line x1="1024" y1="604" x2="916" y2="768" stroke="#0492cd" stroke-width="4"/>
      <line x1="1024" y1="694" x2="975" y2="768" stroke="#0555a3" stroke-width="3"/>
    </g>
  </svg>

  <h1 class="section-badge">POM<br>ORIGINAL<br>WEB<br>SERIES</h1>

  <ul class="content-list">
    <li>Upside Ledge gives you a peek into the entrepreneur 2.0 and what it is like running a cannabis business.</li>
    <li class="package-link">See leadership package</li>
  </ul>

  <div class="brand-mark">POM</div>
  <div class="page-number">6</div>
</main>
</body>
</html>
```